KBT Business Cards

We require business cards for our business. We would like a matte black back to the card, with our logo centred in the middle. The front side of the card is open to design.

Target Market(s)

Clients looking for legal services (professional)

Industry/Entity Type

Legal

Contact Information for Business Card

Doran Kelbrath
Partner
Mobile: 0461 738 524
Email: doran@kbtlaw.co
Website: www.kbtlaw.co
Level 3, 118 Wendmore Street
Sydney NSW 2000

Font styles to use
Other font styles liked:
• Avenir

Colors
f04a50
ffffff
1b1b1b

Requirements
Must have
• Black back with logo included in the centre of the card.
• Our font is Avenir.

```html
<!DOCTYPE html>
<html lang="en">
<head>
<meta charset="utf-8">
<title>KBT Legal — Business Cards</title>
<link rel="stylesheet" href="https://fonts.googleapis.com/css2?family=Nunito+Sans:wght@400;600;700;800&display=swap">
<style>
  :root {
    --accent: #f04a50;
    --accent-deep: #d6244a;
    --white: #ffffff;
    --card: #1b1b1b;
    --card-light: #2e2e2e;
    --muted: #c9c9c9;
    --rule: #5a5a5a;
    --stage-light: #e6e7e8;
    --stage-dark: #a7a8aa;
  }
  * { margin: 0; padding: 0; box-sizing: border-box; }
  html, body { width: 1200px; height: 1090px; overflow: hidden; }
  body {
    position: relative;
    background: linear-gradient(90deg, var(--stage-light) 0%, #cfd0d2 55%, var(--stage-dark) 100%);
    font-family: "Nunito Sans", "Avenir", sans-serif;
    color: var(--white);
  }
  .card {
    position: absolute;
    width: 758px;
    height: 434px;
  }
  .card--front { left: 85px; top: 91px; }
  .card--back { left: 337px; top: 567px; }
  .card__face {
    position: absolute; inset: 0;
    background: radial-gradient(ellipse at 50% 45%, var(--card-light) 0%, var(--card) 70%);
    clip-path: polygon(100px 0, 100% 0, 100% calc(100% - 100px), calc(100% - 100px) 100%, 0 100%, 0 100px);
  }
  .card__corner { position: absolute; inset: 0; width: 758px; height: 434px; }

  .brand {
    position: absolute;
    display: flex; align-items: center; gap: 22px;
  }
  .brand__mark { width: 34px; height: 34px; background: var(--accent-deep); }
  .brand__name {
    font-weight: 800; color: var(--white);
    line-height: 1; letter-spacing: 0.5px;
  }
  .card--front .brand { left: 58px; top: 190px; }
  .card--front .brand__name { font-size: 40px; }
  .card--back .brand { left: 50%; top: 50%; transform: translate(-50%, -62%); }
  .card--back .brand__mark { width: 44px; height: 44px; }
  .card--back .brand__name { font-size: 54px; }

  .divider {
    position: absolute; left: 390px; top: 94px;
    width: 2px; height: 242px; background: var(--rule);
  }
  .contact { position: absolute; left: 421px; top: 92px; }
  .contact__name {
    font-size: 24px; font-weight: 700; color: var(--accent-deep);
    letter-spacing: 0.6px; text-transform: uppercase; line-height: 1.1;
  }
  .contact__role {
    font-size: 18px; color: var(--muted); text-transform: uppercase;
    letter-spacing: 0.5px; margin-top: 4px;
  }
  .contact__address {
    font-style: normal; font-size: 19px; color: var(--muted);
    line-height: 29px; margin-top: 20px;
  }
  .contact__list { list-style: none; margin-top: 18px; }
  .contact__item {
    display: flex; align-items: center; gap: 10px;
    font-size: 19px; color: var(--muted); height: 31px;
  }
  .contact__icon { width: 18px; height: 18px; flex: none; }

  .web {
    position: absolute; left: 0; right: 0; top: 378px;
    text-align: center; font-size: 21px; letter-spacing: 5px; color: var(--white);
  }
  .web__domain { color: var(--accent-deep); font-weight: 700; }
</style>
</head>
<body>

<section class="card card--front" aria-label="Business card front">
  <div class="card__face"></div>
  <svg class="card__corner" viewBox="0 0 758 434" aria-hidden="true">
    <polygon points="0,100 100,0 136,0 0,136" fill="var(--accent-deep)"/>
    <polygon points="758,334 658,434 622,434 758,298" fill="var(--white)"/>
  </svg>

  <div class="brand">
    <span class="brand__mark"></span>
    <span class="brand__name">KBT LEGAL</span>
  </div>

  <div class="divider"></div>

  <div class="contact">
    <div class="contact__name">Doran Kelbrath</div>
    <div class="contact__role">Partner</div>
    <address class="contact__address">
      Level 3, 118 Wendmore Street<br>
      Sydney NSW 2000
    </address>
    <ul class="contact__list">
      <li class="contact__item">
        <svg class="contact__icon" viewBox="0 0 18 18" aria-hidden="true">
          <circle cx="9" cy="9" r="9" fill="var(--accent-deep)"/>
          <rect x="6" y="3.5" width="6" height="11" rx="1" fill="none" stroke="var(--card)" stroke-width="1.4"/>
          <line x1="8" y1="12.5" x2="10" y2="12.5" stroke="var(--card)" stroke-width="1.2"/>
        </svg>
        0461 738 524
      </li>
      <li class="contact__item">
        <svg class="contact__icon" viewBox="0 0 18 18" aria-hidden="true">
          <rect x="1" y="4" width="16" height="11" fill="var(--accent-deep)"/>
          <polyline points="1,4 9,10.5 17,4" fill="none" stroke="var(--card)" stroke-width="1.4"/>
        </svg>
        doran@kbtlaw.co
      </li>
      <li class="contact__item">
        <svg class="contact__icon" viewBox="0 0 18 18" aria-hidden="true">
          <circle cx="9" cy="9" r="8" fill="none" stroke="var(--accent-deep)" stroke-width="1.6"/>
          <ellipse cx="9" cy="9" rx="3.5" ry="8" fill="none" stroke="var(--accent-deep)" stroke-width="1.4"/>
          <line x1="1" y1="9" x2="17" y2="9" stroke="var(--accent-deep)" stroke-width="1.4"/>
        </svg>
        www.kbtlaw.co
      </li>
    </ul>
  </div>
</section>

<section class="card card--back" aria-label="Business card back">
  <div class="card__face"></div>
  <svg class="card__corner" viewBox="0 0 758 434" aria-hidden="true">
    <polygon points="0,100 100,0 136,0 0,136" fill="var(--accent-deep)"/>
    <polygon points="758,334 658,434 622,434 758,298" fill="var(--white)"/>
  </svg>

  <div class="brand">
    <span class="brand__mark"></span>
    <span class="brand__name">KBT LEGAL</span>
  </div>

  <div class="web">www.<span class="web__domain">kbtlaw</span>.co</div>
</section>

</body>
</html>
```